New Business Card for Web Design/Internet Marketing Company

Looking for a great looking new business card. We are a 10 year old web design, internet marketing and website management company that works mostly with small businesses.

Our new card needs to better match the colors and style of our website, be bold, extremely usable and slightly edgy.

Target Market(s)

Small/Medium businesses that have websites

Industry/Entity Type

Internet

Requirements
Must have
• Front and back design, full color, rounded corners please

Must use the colors/style of our website (JPG provided)

INFO FOR CARDS (as readable as possible please)
Mark Lenner
President/CEO
mark@trelvanmedia.example
Phone: 520-381-7459
Toll Free: 866-381-7459
Address: 4315 W. Calloway Ave. Ste. 140, Tucson, AZ 85792

THINGS I WANT TO PROMOTE (if there is room):
1. Our Website - www.trelvanmedia.example

2. Social Media
Twitter: @trelvanmedia
Facebook: www.facebook.com/trelvanmedia

3. Our Services
Web Design
Internet Marketing
Website Management

```html
<!DOCTYPE html>
<html lang="en">
<head>
<meta charset="utf-8">
<title>Trelvan Media – Business Card</title>
<link rel="stylesheet" href="https://fonts.googleapis.com/css2?family=Open+Sans:wght@400;600;700&display=swap">
<style>
  :root {
    --blue: #0a8fc7;
    --orange: #f07b2a;
    --ink: #4f4f4f;
    --paper: #ffffff;
    --backdrop: #e9e6e2;
  }
  * { box-sizing: border-box; margin: 0; padding: 0; }
  html, body {
    width: 1200px; height: 1058px; overflow: hidden;
    background: var(--backdrop);
    font-family: "Open Sans", Arial, sans-serif;
  }
  .canvas { position: relative; width: 1200px; height: 1058px; }

  .card {
    position: absolute;
    width: 772px; height: 441px;
    background: var(--paper);
    border-radius: 14px;
    box-shadow: 0 2px 8px rgba(0,0,0,0.18);
  }
  .card--front { left: 73px; top: 59px; }
  .card--back  { left: 344px; top: 552px; }

  .brand { position: absolute; display: inline-block; }
  .brand__name {
    font-weight: 700; color: var(--blue);
    font-size: 56px; line-height: 1; letter-spacing: -0.5px;
    white-space: nowrap;
  }
  .brand__tagline {
    text-align: right; color: var(--ink);
    font-size: 19px; margin-top: 4px; white-space: nowrap;
  }
  .card--front .brand { left: 60px; top: 74px; }
  .card--back .brand { left: 50%; transform: translateX(-50%); top: 112px; }

  .contact {
    position: absolute; left: 44px; top: 218px;
    list-style: none; color: var(--ink); font-size: 19px;
  }
  .contact li { display: flex; align-items: center; height: 28px; }
  .contact svg { width: 15px; height: 15px; margin-right: 9px; fill: var(--ink); flex: none; }

  .address {
    position: absolute; left: 44px; top: 356px;
    font-style: normal; color: var(--ink); font-size: 19px; line-height: 28px;
  }

  .person {
    position: absolute; left: 470px; top: 290px; width: 230px;
    text-align: center; color: var(--blue);
  }
  .person__name { font-size: 28px; font-weight: 700; line-height: 1.2; }
  .person__title { font-size: 20px; line-height: 1.3; }

  .services {
    position: absolute; left: 0; right: 0; top: 266px;
    text-align: center; color: var(--blue);
    font-size: 25px; font-weight: 700; line-height: 33px;
  }
  .services span { white-space: nowrap; margin: 0 8px; }
  .services span::before {
    content: ""; display: inline-block;
    width: 11px; height: 11px; border-radius: 50%;
    background: var(--orange); margin-right: 9px; vertical-align: 3px;
  }

  .social {
    position: absolute; left: 0; right: 0; top: 372px;
    display: flex; justify-content: center; gap: 22px;
    color: var(--ink); font-size: 22px;
  }
  .social__item { display: flex; align-items: center; }
  .social__mark {
    width: 20px; height: 20px; border-radius: 3px;
    background: var(--blue); margin-right: 8px;
  }
</style>
</head>
<body>
<div class="canvas">

  <section class="card card--front" aria-label="Card front">
    <div class="brand">
      <div class="brand__name">Trelvan Media</div>
      <div class="brand__tagline">Built to be Found</div>
    </div>

    <ul class="contact">
      <li><svg viewBox="0 0 16 16" aria-hidden="true"><path d="M3.6 1.2l2.4 2.6-1.3 1.7c.9 2 2.3 3.5 4.3 4.5l1.6-1.3 2.7 2.3-1.5 2.3C7 13 2.6 8.4 1.4 2.9z"/></svg>866-381-7459</li>
      <li><svg viewBox="0 0 16 16" aria-hidden="true"><path d="M3.6 1.2l2.4 2.6-1.3 1.7c.9 2 2.3 3.5 4.3 4.5l1.6-1.3 2.7 2.3-1.5 2.3C7 13 2.6 8.4 1.4 2.9z"/></svg>520-381-7459</li>
      <li><svg viewBox="0 0 16 16" aria-hidden="true"><path d="M1 5l7-4 7 4v9H1zm1.5 1.2v6.6h11V6.2L8 9.5z"/></svg>mark@trelvanmedia.example</li>
      <li><svg viewBox="0 0 16 16" aria-hidden="true"><circle cx="8" cy="8" r="7"/></svg>www.trelvanmedia.example</li>
    </ul>

    <address class="address">
      4315 W. Calloway Ave. Ste. 140<br>
      Tucson, AZ 85792
    </address>

    <div class="person">
      <div class="person__name">Mark Lenner</div>
      <div class="person__title">President/CEO</div>
    </div>
  </section>

  <section class="card card--back" aria-label="Card back">
    <div class="brand">
      <div class="brand__name">Trelvan Media</div>
      <div class="brand__tagline">Built to be Found</div>
    </div>

    <div class="services">
      <span>Web Design</span><span>Internet Marketing</span><br>
      <span>Website Management</span>
    </div>

    <div class="social">
      <div class="social__item"><span class="social__mark"></span>@trelvanmedia</div>
      <div class="social__item"><span class="social__mark"></span>trelvanmedia</div>
    </div>
  </section>

</div>
</body>
</html>
```